High value cover design for an A4 ideation pad.

The product is NOT A BOOK.

It's an A4 ideation pad for professionals, designers and creators who handwrite their ideas. Visualise creators like Milo Varnet, Owen Plaskit and Gregor Lunwick in your mind's eye.

I'm looking for a cover design for the ideation pad. Both front and back.

It should look, feel and convey the following.

--> A handcrafted product experience

--> High value & Elegance

--> Inspiration

Mandatory --> See Uploaded Files --> Files 1, 5 & 6

Target Market(s)

- Designers

-Creative Professionals

- Entrepreneurs

who handwrite their ideas. Visualise creators like Milo Varnet, Owen Plaskit and Gregor Lunwick in your mind's eye.

Industry/Entity Type

Stationary

Font styles to use
Script
Other font styles liked:
• Calligraphy

Colors
fbed22

Requirements
Must have
• Title text - Quiet Kettle Notes

-Text in gold on brown leather background to convey high value for the front cover.

--> High value & Elegance

--> Inspiration

--> Should compel the customers to pick up and own the idea pad
Nice to have
• That's my take but other ideas are welcome
Should not have
• Must not convey

- low value

```html
<!DOCTYPE html>
<html lang="en">
<head>
<meta charset="utf-8">
<title>Quiet Kettle Notes — Ideation Pad Cover</title>
<link rel="stylesheet" href="https://fonts.googleapis.com/css2?family=Great+Vibes&display=swap">
<style>
  :root {
    --backdrop: #e4e4e4;
    --leather-light: #c2622f;
    --leather-mid: #b3572a;
    --leather-dark: #a44c24;
    --ring-line: #d8642d;
    --gold-bright: #fbed22;
    --gold-deep: #e2a514;
    --ornament-gold: #f2c21a;
    --patch: rgba(222, 120, 70, 0.45);
  }
  * { box-sizing: border-box; margin: 0; padding: 0; }
  html, body { width: 1200px; height: 900px; overflow: hidden; }
  body { background: var(--backdrop); position: relative; }

  .cover {
    position: absolute;
    top: 150px;
    width: 420px;
    height: 608px;
    background: radial-gradient(ellipse at 50% 40%, var(--leather-light), var(--leather-mid) 60%, var(--leather-dark));
    overflow: hidden;
  }
  .cover--front { left: 134px; }
  .cover--back { left: 652px; width: 422px; height: 610px; }

  .rings { position: absolute; inset: 0; width: 100%; height: 100%; }
  .rings circle { fill: none; stroke: var(--ring-line); stroke-width: 4; opacity: 0.85; }

  .corner-mark {
    position: absolute;
    width: 52px; height: 52px;
    background: var(--patch);
    border-radius: 6px;
    transform: rotate(45deg);
  }

  .title-ornament {
    position: absolute;
    left: 6px; top: 30px;
    width: 408px; height: 218px;
    border-radius: 50% / 40%;
    background: radial-gradient(ellipse at center, rgba(251, 237, 34, 0.08) 55%, rgba(242, 194, 26, 0.55) 62%, rgba(242, 194, 26, 0.0) 72%);
  }
  .title {
    position: absolute;
    left: 0; right: 0; top: 106px;
    text-align: center;
    font-family: "Great Vibes", cursive;
    font-size: 46px;
    line-height: 1;
    color: var(--gold-bright);
    background: linear-gradient(180deg, var(--gold-bright), var(--gold-deep));
    -webkit-background-clip: text;
    background-clip: text;
    -webkit-text-fill-color: transparent;
  }

  .emblem {
    position: absolute;
    width: 216px; height: 240px;
    border-radius: 50%;
    background: conic-gradient(from -30deg, #f3c90c, #c4101a 60deg, #1425a8 120deg, #12a01c 180deg, #c4101a 240deg, #1425a8 300deg, #f3c90c);
    opacity: 0.9;
  }
  .cover--front .emblem { left: 104px; top: 310px; }
  .cover--back .emblem { left: 104px; top: 187px; }
</style>
</head>
<body>

  <section class="cover cover--front" aria-label="Front cover">
    <svg class="rings" viewBox="0 0 420 608" aria-hidden="true">
      <circle cx="213" cy="428" r="172"/>
      <circle cx="213" cy="428" r="150"/>
    </svg>
    <div class="corner-mark" style="left:18px; top:26px;" role="img" aria-label="Faint pen nib mark"></div>
    <div class="corner-mark" style="right:18px; top:26px;" role="img" aria-label="Faint pen nib mark"></div>
    <div class="corner-mark" style="left:28px; top:276px;" role="img" aria-label="Faint pen nib mark"></div>
    <div class="corner-mark" style="right:28px; top:276px;" role="img" aria-label="Faint pen nib mark"></div>
    <div class="corner-mark" style="left:18px; bottom:18px;" role="img" aria-label="Faint pen nib mark"></div>
    <div class="corner-mark" style="right:18px; bottom:18px;" role="img" aria-label="Faint pen nib mark"></div>

    <div class="title-ornament" role="img" aria-label="Gold leaf ornamental frame around the title"></div>
    <h1 class="title">Quiet Kettle Notes</h1>

    <div class="emblem" role="img" aria-label="Six coloured pen nibs arranged as a flower"></div>
  </section>

  <section class="cover cover--back" aria-label="Back cover">
    <svg class="rings" viewBox="0 0 422 610" aria-hidden="true">
      <circle cx="215" cy="304" r="202"/>
      <circle cx="215" cy="304" r="176"/>
      <circle cx="215" cy="304" r="142"/>
    </svg>
    <div class="corner-mark" style="left:18px; top:26px;" role="img" aria-label="Faint pen nib mark"></div>
    <div class="corner-mark" style="right:18px; top:26px;" role="img" aria-label="Faint pen nib mark"></div>
    <div class="corner-mark" style="left:18px; bottom:18px;" role="img" aria-label="Faint pen nib mark"></div>
    <div class="corner-mark" style="right:18px; bottom:18px;" role="img" aria-label="Faint pen nib mark"></div>

    <div class="emblem" role="img" aria-label="Six coloured pen nibs arranged as a flower"></div>
  </section>

</body>
</html>
```